My Web Development Portfolio site

I'm a web developer and I need a web design that can showcase my web development portfolio. I like most of the websites from this link: http://www.lumivexa.com/portfolios/examples-503917. My ideal design should be modern, clean and fun. I will let the designer decided the color theme for the website.

Target Market(s)

Potential Employers.

Number of Pages Required

1 page

Requirements
Must have
• - Menu bar that includes at least: About Me, Blog, Contact, Project/Work
• - Excellent color theme
• - Use the logo I provided (see attachment)
Nice to have
• - Some animation
• - Fun yet modern design

```html
<!DOCTYPE html>
<html lang="en">
<head>
<meta charset="utf-8">
<title>Bytetrail — Web Development Portfolio</title>
<link rel="stylesheet" href="https://fonts.googleapis.com/css2?family=Questrial&family=Raleway:wght@400;500;600;700&family=Archivo+Black&display=swap">
<style>
:root{
  --orange:#f0844c;
  --orange-soft:#f6a26e;
  --hero-a:#ffb400;
  --hero-b:#ff9a00;
  --ink:#1d1d1d;
  --text:#3a3a3a;
  --muted:#8a8a8a;
  --light:#f6f6f6;
  --panel:#ececec;
  --footer:#2c2c2c;
  --footer-deep:#1e1e1e;
  --white:#ffffff;
}
*{box-sizing:border-box;margin:0;padding:0}
html,body{width:1200px;height:3267px;overflow:hidden}
body{font-family:'Raleway',sans-serif;color:var(--text);background:var(--white);position:relative}
section,header,footer{position:absolute;left:0;width:1200px}
.abs{position:absolute}
.heading{font-family:'Questrial',sans-serif;font-weight:400;color:var(--ink);font-size:40px;letter-spacing:.5px}
.rule{position:absolute;height:2px;width:52px;background:var(--orange)}

/* header */
.site-header{top:0;height:100px;background:var(--white)}
.brand{left:98px;top:22px;display:flex;align-items:center;gap:10px}
.brand-dot{width:22px;height:22px;border-radius:50%;background:var(--orange)}
.brand-name{font-family:'Raleway',sans-serif;font-size:26px;font-weight:500;color:var(--orange);letter-spacing:1px}
.main-nav{right:98px;top:64px;display:flex;gap:56px;font-size:13px;color:var(--ink)}
.main-nav a{color:inherit;text-decoration:none;position:relative}
.main-nav a.is-active{color:var(--orange)}
.main-nav a.is-active::after{content:"";position:absolute;left:-8px;right:-8px;bottom:-10px;height:2px;background:var(--orange)}

/* hero */
.hero{top:100px;height:552px;background:radial-gradient(ellipse at 50% 40%,var(--hero-a) 0%,var(--hero-b) 80%)}
.tool-badge{position:absolute;border-radius:50%;background:var(--white);box-shadow:0 4px 10px rgba(0,0,0,.18);display:flex;align-items:center;justify-content:center}
.tool-badge span{display:block;border-radius:50%}
.hero-art{left:200px;top:310px;width:250px;height:180px;border-radius:40%;background:radial-gradient(ellipse at 40% 40%,rgba(190,100,0,.22),rgba(190,100,0,0) 70%)}
.hero-title{left:0;width:1200px;top:348px;text-align:center;font-family:'Archivo Black',sans-serif;font-size:36px;line-height:44px;color:var(--ink)}
.hero-button{left:500px;top:422px;width:200px;height:44px;border:2px solid var(--ink);font-size:13px;font-weight:700;color:var(--ink);display:flex;align-items:center;justify-content:center;letter-spacing:.5px}
.slider-dots{left:566px;top:508px;display:flex;gap:8px}
.slider-dots i{width:9px;height:9px;border-radius:50%;background:rgba(255,255,255,.55)}
.slider-dots i.is-current{background:transparent;border:2px solid var(--ink)}
.slider-arrow{top:240px}

/* about */
.about{top:652px;height:378px;background:var(--white)}
.about-mark{left:100px;top:48px;width:240px;height:240px;border-radius:50%;background:#fbd9c5}
.about .heading{left:495px;top:52px}
.about .rule{left:495px;top:126px}
.about-copy{left:495px;top:150px;width:610px;font-size:13px;line-height:23.5px}
.outline-button{left:495px;top:268px;width:172px;height:46px;border:2px solid var(--orange-soft);color:var(--orange);font-size:13px;font-weight:600;display:flex;align-items:center;justify-content:center;gap:10px;border-radius:2px}

/* projects */
.projects{top:1030px;height:1128px;background:var(--light)}
.projects .heading{left:0;width:1200px;text-align:center;top:48px}
.hex{position:absolute;width:232px;height:266px;filter:drop-shadow(0 3px 6px rgba(0,0,0,.18))}
.hex-frame,.hex-fill{position:absolute;clip-path:polygon(50% 0,100% 25%,100% 75%,50% 100%,0 75%,0 25%)}
.hex-frame{inset:0;background:var(--white)}
.hex-fill{inset:8px}
.hex.is-hover .hex-frame{background:var(--orange-soft)}
.hex-caption{position:absolute;left:8px;right:8px;top:124px;height:70px;background:rgba(30,30,30,.78);color:var(--white);text-align:center;padding-top:14px}
.hex-caption b{display:block;font-size:13px;letter-spacing:.5px}
.hex-caption small{display:block;font-size:12px;color:#bbb;margin-top:8px}

/* blog */
.blog{top:2158px;height:602px;background:var(--white)}
.blog .heading{left:0;width:1200px;text-align:center;top:46px}
.blog .rule{left:574px;top:124px}
.post{position:absolute;top:167px;width:316px}
.post-thumb{height:206px}
.post-title{margin-top:24px;font-size:15px;font-weight:700;color:var(--ink);letter-spacing:.3px}
.post-date{margin-top:10px;font-size:12px;color:var(--muted)}
.post-text{margin-top:14px;font-size:12.5px;line-height:21px}
.read-more{margin-top:12px;font-size:12px;color:var(--orange);font-weight:600;display:flex;align-items:center;gap:6px}

/* newsletter */
.newsletter{top:2760px;height:255px;background:var(--panel)}
.newsletter .heading{left:0;width:1200px;text-align:center;top:48px}
.newsletter .rule{left:574px;top:118px}
.field{position:absolute;top:165px;height:40px;background:var(--white);border:1px solid #dcdcdc;font-size:12px;color:#666;padding:12px 10px}
.signup-button{position:absolute;left:905px;top:165px;width:197px;height:40px;background:var(--orange);color:var(--white);font-size:13px;font-weight:700;display:flex;align-items:center;justify-content:center;letter-spacing:.5px}

/* footer */
.site-footer{top:3015px;height:190px;background:var(--footer)}
.footer-divider{position:absolute;top:48px;width:1px;height:96px;background:#4a4a4a}
.footer-brand{left:230px;top:60px;width:175px;display:flex;flex-direction:column;align-items:center;gap:8px}
.footer-brand .brand-dot{width:26px;height:26px}
.footer-contact{position:absolute;top:52px;text-align:center;color:var(--white);font-size:17px}
.contact-icon{width:50px;height:50px;border-radius:50%;background:var(--orange);border:3px solid #f7a47a;margin:0 auto 18px;display:flex;align-items:center;justify-content:center}
.legal-bar{position:absolute;left:0;top:3205px;width:1200px;height:62px;background:var(--footer-deep)}
.legal-bar p{position:absolute;left:98px;top:24px;font-size:12px;color:var(--white);font-weight:600}
.social{position:absolute;right:96px;top:14px;display:flex;gap:10px}
.social i{width:36px;height:36px;border-radius:50%;border:2px solid var(--white)}
</style>
</head>
<body>

<header class="site-header">
  <div class="abs brand"><span class="brand-dot"></span><span class="brand-name">bytetrail</span></div>
  <nav class="abs main-nav">
    <a href="#" class="is-active">Home</a>
    <a href="#">About Me</a>
    <a href="#">Project/Work</a>
    <a href="#">Blog</a>
    <a href="#">Contact</a>
  </nav>
</header>

<section class="hero">
  <svg class="abs slider-arrow" style="left:62px" width="40" height="70" viewBox="0 0 40 70"><path d="M36 2 4 35l32 33" fill="none" stroke="rgba(255,255,255,.55)" stroke-width="2"/></svg>
  <svg class="abs slider-arrow" style="left:1098px" width="40" height="70" viewBox="0 0 40 70"><path d="M4 2l32 33L4 68" fill="none" stroke="rgba(255,255,255,.55)" stroke-width="2"/></svg>

  <div class="tool-badge" style="left:190px;top:140px;width:140px;height:140px"><span style="width:116px;height:116px;background:#f7a625"></span></div>
  <div class="tool-badge" style="left:836px;top:140px;width:140px;height:140px"><span style="width:116px;height:116px;background:#2a78c8"></span></div>
  <div class="tool-badge" style="left:310px;top:112px;width:180px;height:180px"><span style="width:154px;height:154px;background:#2d6fb7"></span></div>
  <div class="tool-badge" style="left:680px;top:112px;width:180px;height:180px"><span style="width:154px;height:154px;background:#e34f26"></span></div>
  <div class="tool-badge" style="left:478px;top:60px;width:228px;height:228px"><span role="img" aria-label="Painter's easel and palette illustration" style="width:200px;height:200px;background:radial-gradient(circle,#c99a5c 0%,#7a5633 90%)"></span></div>

  <div class="abs hero-art" role="img" aria-label="Paper plane with a dashed looping flight path"></div>
  <h1 class="abs hero-title">Web Design &amp; Development</h1>
  <div class="abs hero-button">SEE OUR PORTFOLIO</div>
  <div class="abs slider-dots"><i class="is-current"></i><i></i><i></i><i></i></div>
</section>

<section class="about">
  <div class="abs about-mark"></div>
  <h2 class="abs heading">About Me</h2>
  <span class="rule"></span>
  <p class="abs about-copy">Lorem ipsum dolor sit amet, consectetuer adipiscing elit, sed diam nonummy nibh euismodm tincidunt ut laoreet dolore magna aliquam erat volutpat. Ut wisi enim ad minim veniam, quismi nostrud exerci tation ullamcorper suscipit lobortis nisl ut aliquip ex eam commodo consequat. Duis autem vel eum iriure dolor in hendrerit in vulputate facilisis.</p>
  <div class="abs outline-button">
    <svg width="16" height="12" viewBox="0 0 16 12"><rect width="16" height="12" rx="1" fill="var(--orange)"/><path d="M1 1l7 6 7-6" fill="none" stroke="#fff" stroke-width="1.5"/></svg>
    MESSAGE ME
  </div>
</section>

<section class="projects">
  <h2 class="abs heading">Project / Work</h2>

  <div class="hex is-hover" style="left:120px;top:172px">
    <div class="hex-frame"></div>
    <div class="hex-fill" role="img" aria-label="Website project preview with flowers and a profile card" style="background:linear-gradient(135deg,#e9e4df,#6b6462)"></div>
    <div class="hex-caption"><b>CONSECTETUER</b><small>Duis autem vel eum iriu</small></div>
  </div>
  <div class="hex" style="left:484px;top:172px"><div class="hex-frame"></div><div class="hex-fill" role="img" aria-label="Event poster project in cream and red" style="background:linear-gradient(150deg,#f3ecd6 40%,#d9352c)"></div></div>
  <div class="hex" style="left:848px;top:172px"><div class="hex-frame"></div><div class="hex-fill" role="img" aria-label="Green product website project" style="background:linear-gradient(160deg,#a6cf58,#e8f1d8)"></div></div>

  <div class="hex" style="left:120px;top:488px"><div class="hex-frame"></div><div class="hex-fill" role="img" aria-label="Colourful retro web layout project" style="background:radial-gradient(circle at 55% 55%,#f2c12e 0 30%,#a3325f 60%)"></div></div>
  <div class="hex" style="left:484px;top:488px"><div class="hex-frame"></div><div class="hex-fill" role="img" aria-label="Packaging design project in grey and green" style="background:linear-gradient(140deg,#dcdcdc,#3a3a3a 70%,#a8c93a)"></div></div>
  <div class="hex" style="left:848px;top:488px"><div class="hex-frame"></div><div class="hex-fill" role="img" aria-label="Developer profile page project" style="background:linear-gradient(160deg,#5a4f4b,#c9c2bd)"></div></div>

  <div class="hex" style="left:120px;top:808px"><div class="hex-frame"></div><div class="hex-fill" role="img" aria-label="Photographer portfolio project" style="background:linear-gradient(150deg,#c74a4a,#e6dedc 70%)"></div></div>
  <div class="hex" style="left:484px;top:808px"><div class="hex-frame"></div><div class="hex-fill" role="img" aria-label="Vintage styled website project" style="background:linear-gradient(170deg,#4a4644,#b39a7f)"></div></div>
  <div class="hex" style="left:848px;top:808px"><div class="hex-frame"></div><div class="hex-fill" role="img" aria-label="Business profile and mobile app project" style="background:linear-gradient(150deg,#2c3d5c,#8aa0b8)"></div></div>
</section>

<section class="blog">
  <h2 class="abs heading">Latest Blog</h2>
  <span class="rule"></span>
  <svg class="abs" style="left:44px;top:236px" width="20" height="52" viewBox="0 0 20 52"><path d="M18 2 2 26l16 24" fill="none" stroke="#cfcfcf" stroke-width="2"/></svg>
  <svg class="abs" style="left:1136px;top:236px" width="20" height="52" viewBox="0 0 20 52"><path d="M2 2l16 24L2 50" fill="none" stroke="#cfcfcf" stroke-width="2"/></svg>

  <article class="post" style="left:98px">
    <div class="post-thumb" role="img" aria-label="Illustrated postage stamps" style="background:linear-gradient(90deg,#e8b63c,#d0463b 50%,#3fa5b5)"></div>
    <h3 class="post-title">CONSECTETUER ADIPISCING</h3>
    <p class="post-date">April 21, 2016</p>
    <p class="post-text">Ut wisi enim ad minim veniam, quismi nostrudml exerci tation ullamcorper suscipit lobortis nisl un aliquip ex eam commodo consequat.</p>
    <p class="read-more">Read More <svg width="18" height="8" viewBox="0 0 18 8"><path d="M0 4h16M13 1l3 3-3 3" fill="none" stroke="var(--orange)" stroke-width="1.2"/></svg></p>
  </article>
  <article class="post" style="left:442px">
    <div class="post-thumb" role="img" aria-label="Cartoon landing page illustration" style="background:linear-gradient(180deg,#f2ece8,#ddd2cb)"></div>
    <h3 class="post-title">CONSECTETUER ADIPISCING</h3>
    <p class="post-date">April 21, 2016</p>
    <p class="post-text">Ut wisi enim ad minim veniam, quismi nostrudml exerci tation ullamcorper suscipit lobortis nisl un aliquip ex eam commodo consequat.</p>
    <p class="read-more">Read More <svg width="18" height="8" viewBox="0 0 18 8"><path d="M0 4h16M13 1l3 3-3 3" fill="none" stroke="var(--orange)" stroke-width="1.2"/></svg></p>
  </article>
  <article class="post" style="left:785px">
    <div class="post-thumb" role="img" aria-label="Vintage hot rod car poster" style="background:linear-gradient(180deg,#d9cfb4,#6e8b8a)"></div>
    <h3 class="post-title">CONSECTETUER ADIPISCING</h3>
    <p class="post-date">April 21, 2016</p>
    <p class="post-text">Ut wisi enim ad minim veniam, quismi nostrudml exerci tation ullamcorper suscipit lobortis nisl un aliquip ex eam commodo consequat.</p>
    <p class="read-more">Read More <svg width="18" height="8" viewBox="0 0 18 8"><path d="M0 4h16M13 1l3 3-3 3" fill="none" stroke="var(--orange)" stroke-width="1.2"/></svg></p>
  </article>
</section>

<section class="newsletter">
  <h2 class="abs heading">Newsletter Signup</h2>
  <span class="rule"></span>
  <div class="field" style="left:98px;width:394px">Name</div>
  <div class="field" style="left:502px;width:394px">Email</div>
  <div class="signup-button">SIGNUP</div>
</section>

<footer class="site-footer">
  <div class="abs footer-brand"><span class="brand-dot"></span><span class="brand-name">bytetrail</span></div>
  <span class="footer-divider" style="left:456px"></span>
  <div class="footer-contact" style="left:488px;width:200px">
    <div class="contact-icon"><svg width="22" height="22" viewBox="0 0 24 24"><path d="M6.6 10.8a15 15 0 0 0 6.6 6.6l2.2-2.2c.3-.3.7-.4 1-.2 1.1.4 2.3.6 3.6.6.6 0 1 .4 1 1V20c0 .6-.4 1-1 1A17 17 0 0 1 3 4c0-.6.4-1 1-1h3.5c.6 0 1 .4 1 1 0 1.3.2 2.5.6 3.6.1.3 0 .7-.2 1z" fill="#fff"/></svg></div>
    +123 555 0142
  </div>
  <span class="footer-divider" style="left:716px"></span>
  <div class="footer-contact" style="left:760px;width:220px">
    <div class="contact-icon"><svg width="20" height="15" viewBox="0 0 16 12"><rect width="16" height="12" rx="1" fill="#fff"/><path d="M1 1l7 6 7-6" fill="none" stroke="var(--orange)" stroke-width="1.5"/></svg></div>
    info@bytetrail.com
  </div>
</footer>
<div class="legal-bar">
  <p>© 2016 Bytetrail. All rights reserved.</p>
  <div class="social"><i></i><i></i><i></i><i></i></div>
</div>

</body>
</html>
```